VELK Redesign

Make a more modern looking Homepage. Our page: www.velk-example.at
Should look like:
www.tarnok-example.com/at/de/
https://web.dovrand-example.com
https://id.pallomere-example.com

Target Market(s)

furniture industry

Number of Pages Required

1 page

Font styles to use
Sans Serif

Colors
3176b5

```html
<!DOCTYPE html>
<html lang="en">
<head>
<meta charset="utf-8">
<title>VELK – Furniture Fittings</title>
<link rel="stylesheet" href="https://fonts.googleapis.com/css2?family=Montserrat:wght@400;500&family=Open+Sans:wght@400;600&display=swap">
<style>
:root{
  --brand:#3176b5;
  --brand-dark:#2a64a6;
  --ink:#2b2b2b;
  --muted:#6b6b6b;
  --header:rgba(26,42,66,.92);
  --footer:#282828;
  --footer-text:#9a9a9a;
  --line:#d6d6d6;
  --white:#fff;
}
*{margin:0;padding:0;box-sizing:border-box}
html,body{width:1200px;height:2406px;overflow:hidden;background:var(--white)}
body{position:relative;font-family:"Open Sans",Arial,sans-serif;color:var(--ink)}
.abs{position:absolute}
a{color:inherit;text-decoration:none}

/* header */
.site-header{left:0;top:0;width:1200px;height:64px;background:var(--header);z-index:2}
.brand{left:144px;top:14px;display:flex;align-items:center;gap:10px;color:var(--white);font-family:"Montserrat",sans-serif;font-size:30px;font-weight:400;letter-spacing:4px;line-height:36px}
.brand-mark{width:30px;height:30px;border-radius:50%;background:var(--white)}
.main-nav{top:24px;font-size:12px;color:#e6ebf2;white-space:nowrap}
.lang{left:1010px;top:24px;font-size:12px;color:#e6ebf2;white-space:nowrap}

/* hero */
.hero{left:0;top:0;width:1200px;height:614px;background:linear-gradient(135deg,#9a9a9a 0%,#b9b9b7 40%,#8f8f8d 100%)}
.hero-caption{left:144px;top:277px;width:357px;height:126px;background:rgba(49,118,181,.9);color:var(--white);padding:10px 16px 0 17px;overflow:hidden}
.hero-caption h1{font-family:"Open Sans",sans-serif;font-weight:400;font-size:36px;line-height:52px;white-space:nowrap;letter-spacing:-.2px}
.hero-caption p{font-family:"Montserrat",sans-serif;font-size:14.5px;line-height:26px;padding-left:3px;white-space:nowrap}
.hero-arrow{top:322px;width:24px;height:34px;background:rgba(40,40,40,.75)}

/* welcome */
.section-title{left:0;width:1200px;text-align:center;font-family:"Montserrat",sans-serif;font-weight:400;font-size:32px;color:var(--brand);white-space:nowrap}
.welcome-text{left:146px;top:736px;width:908px;text-align:center;font-size:12.3px;line-height:22px;color:var(--muted)}
.tile-img{top:829px;width:296px;height:201px}
.tile-label{top:1040px;width:296px;text-align:center;font-family:"Montserrat",sans-serif;font-size:16px;color:var(--brand)}

/* banners */
.banner-img{top:1139px;height:319px}
.banner-label{top:1466px;text-align:center;font-family:"Montserrat",sans-serif;font-size:16px;color:var(--ink)}
.rule{left:0;top:1497px;width:1200px;height:1px;background:var(--line)}

/* news */
.news-card{top:1630px;width:287px;height:319px;background:var(--white);border:1px solid #ececec}
.news-card.raised{box-shadow:0 6px 14px rgba(0,0,0,.18);border-color:#e4e4e4}
.news-img{height:179px}
.news-date{margin:24px 14px 0;font-family:"Montserrat",sans-serif;font-size:13px;color:var(--brand)}
.news-text{margin:6px 14px 0;font-family:"Montserrat",sans-serif;font-size:14.4px;line-height:22.5px;color:var(--ink)}
.btn{left:539px;top:1989px;width:120px;height:40px;background:var(--brand-dark);color:var(--white);text-align:center;line-height:40px;font-family:"Montserrat",sans-serif;font-size:14px}

/* footer */
.site-footer{left:0;top:2109px;width:1200px;height:297px;background:var(--footer)}
.footer-heading{top:2160px;font-family:"Montserrat",sans-serif;font-weight:400;font-size:19px;color:#f1f1f1;white-space:nowrap}
.footer-links{top:2199px;list-style:none;font-size:12px;line-height:27.4px;color:var(--footer-text);white-space:nowrap}
.newsletter{left:662px;top:2202px;width:218px;height:45px;background:#dedede;display:flex;align-items:center;justify-content:space-between;padding:0 12px 0 16px;font-size:12px;color:#444}
.social{top:2202px;width:22px;height:22px;border-radius:50%;background:#a8a8a8}
.footer-rule{left:144px;top:2331px;width:910px;height:1px;background:#4a4a4a}
.copyright{left:0;top:2360px;width:1200px;text-align:center;font-size:12px;color:#f1f1f1}
</style>
</head>
<body>

<div class="hero abs" role="img" aria-label="Photo of dark and copper-finished furniture handles and knobs on a grey concrete surface"></div>

<header class="site-header abs">
  <a class="brand abs" href="#"><span class="brand-mark"></span>VELK</a>
  <nav>
    <a class="main-nav abs" style="left:483px;color:#fff" href="#">Brand New</a>
    <a class="main-nav abs" style="left:566px" href="#">Catalogue Configurator</a>
    <a class="main-nav abs" style="left:709px" href="#">Light Configurator</a>
    <a class="main-nav abs" style="left:826px" href="#">Lamps</a>
    <a class="main-nav abs" style="left:887px" href="#">Register</a>
    <a class="main-nav abs" style="left:955px" href="#">Login</a>
  </nav>
  <div class="lang abs">DE &nbsp;|&nbsp; <span style="color:#fff">EN</span></div>
</header>

<div class="hero-caption abs">
  <h1>Furniture Fittings</h1>
  <p>Functionality meets Design.<br>Be inspired by the new VELK-Collection.</p>
</div>
<div class="hero-arrow abs" style="left:0">
  <svg width="24" height="34" viewBox="0 0 24 34"><path d="M15 10 L9 17 L15 24" fill="none" stroke="#fff" stroke-width="1.6"/></svg>
</div>
<div class="hero-arrow abs" style="left:1176px">
  <svg width="24" height="34" viewBox="0 0 24 34"><path d="M9 10 L15 17 L9 24" fill="none" stroke="#fff" stroke-width="1.6"/></svg>
</div>

<h2 class="section-title abs" style="top:686px">Welcome to VELK</h2>
<p class="welcome-text abs">Fusce nec leo ac urna pulvinar auctor. Mauris bibendum fringilla velit. Nulla in lorem at massa pellentesque posuere. Nulla tristique posuere molestie. Aliquam erat volutpat. Etiam quis aliquet risus. Duis ornare erat eget magna dapibus, in accumsan quam pharetra. Nam tempus, quam in bibendum vulputate, sapien dolor viverra nisl, vitae euismod elit turpis et nulla. Aliquam erat volutpat.</p>

<div class="tile-img abs" style="left:144px;background:linear-gradient(90deg,#7d8186,#9ea1a4 60%,#c9c9c6)" role="img" aria-label="Display wall of sample handles in a showroom"></div>
<div class="tile-img abs" style="left:452px;background:linear-gradient(180deg,#8a6a52 0%,#a38670 45%,#e6e6e6 55%,#f1f1f1)" role="img" aria-label="Hand opening a white drawer with an aluminium handle"></div>
<div class="tile-img abs" style="left:759px;background:linear-gradient(135deg,#e9eaeb,#cfd4da 55%,#eef0f2)" role="img" aria-label="LED light bulbs on a white surface"></div>
<a class="tile-label abs" style="left:144px" href="#">Catalogue Configurator</a>
<a class="tile-label abs" style="left:452px" href="#">Light Configurator</a>
<a class="tile-label abs" style="left:759px" href="#">Lamps</a>

<div class="banner-img abs" style="left:0;width:395px;background:linear-gradient(90deg,#e4ded3,#d8d0c4 50%,#eae6df)" role="img" aria-label="Hand gripping a silver handle on a light wooden cabinet door"></div>
<div class="banner-img abs" style="left:403px;width:395px;background:linear-gradient(180deg,#8a7e72,#76675a 60%,#5f5247)" role="img" aria-label="Wooden kitchen drawers with slim metal handles"></div>
<div class="banner-img abs" style="left:804px;width:396px;background:linear-gradient(135deg,#dcdcdc,#c4c0ba 50%,#a9a39b)" role="img" aria-label="Antique bronze and pewter handles on a display board"></div>
<div class="banner-label abs" style="left:0;width:395px">Vestibulum condimentum</div>
<div class="banner-label abs" style="left:403px;width:395px">Fusce sollicitudin</div>
<div class="banner-label abs" style="left:804px;width:396px">Etiam vel massa</div>
<div class="rule abs"></div>

<h2 class="section-title abs" style="top:1571px">Aenean quam sapien faucibus</h2>

<article class="news-card abs" style="left:144px">
  <div class="news-img" style="background:linear-gradient(135deg,#8f8a80,#2f5f9e 55%,#c8c8c8)" role="img" aria-label="Close-up of metal handles on a blue display panel"></div>
  <p class="news-date">16 February, 2019</p>
  <p class="news-text">Proin placerat dapibus gravida. In tristique tristique nulla eget &nbsp;vel tortor accumsan quam.</p>
</article>
<article class="news-card raised abs" style="left:457px">
  <div class="news-img" style="background:linear-gradient(180deg,#9a5b30,#7a3f22 55%,#5a2e1a)" role="img" aria-label="Collection of wooden cabinet doors with assorted handles"></div>
  <p class="news-date">16 February, 2019</p>
  <p class="news-text">Etiam vel massa elementum, bibendum tellus venenatis, feugiat massa.</p>
</article>
<article class="news-card abs" style="left:768px">
  <div class="news-img" style="background:linear-gradient(90deg,#8a8f96,#b9bec4 55%,#dfe2e6)" role="img" aria-label="Craftsman inspecting a metal handle in a workshop"></div>
  <p class="news-date">16 February, 2019</p>
  <p class="news-text">Quisque aliquet nec est vestibulum pulvinar. Pellentesque convallis molestie enim sit amet efficitur.</p>
</article>

<a class="btn abs" href="#">View All</a>

<footer class="site-footer abs"></footer>
<h3 class="footer-heading abs" style="left:144px">Links</h3>
<ul class="footer-links abs" style="left:144px"><li>Brand New</li><li>Catalogue Configurator</li><li>Light Configurator</li><li>Lamps</li></ul>
<ul class="footer-links abs" style="left:289px"><li>Register</li><li>Login</li></ul>
<h3 class="footer-heading abs" style="left:395px">Aliquam</h3>
<ul class="footer-links abs" style="left:395px"><li>Donec vestibulum</li><li>Quisque aliquet</li><li>Pellentesque</li><li>Etiam id</li></ul>
<ul class="footer-links abs" style="left:515px"><li>Fusce vitae</li><li>Aenean placerat</li><li>Vestibulum ante</li><li>Vestibulum eget</li></ul>
<h3 class="footer-heading abs" style="left:662px">Newsletter Signup</h3>
<div class="newsletter abs">
  <span>Email Address</span>
  <svg width="20" height="15" viewBox="0 0 20 15" aria-hidden="true"><rect x="0" y="0" width="20" height="15" rx="1.5" fill="#2b2b2b"/><path d="M1 1.5 L10 8.5 L19 1.5" fill="none" stroke="#dedede" stroke-width="1.6"/></svg>
</div>
<h3 class="footer-heading abs" style="left:937px">Follow us on</h3>
<span class="social abs" style="left:934px" aria-label="Social network 1"></span>
<span class="social abs" style="left:982px" aria-label="Social network 2"></span>
<span class="social abs" style="left:1033px" aria-label="Social network 3"></span>
<div class="footer-rule abs"></div>
<p class="copyright abs">Copyright &nbsp;©&nbsp; 2019 &nbsp;VELK. &nbsp;&nbsp;All rights reserved.</p>

</body>
</html>
```